RB Halden Electric Yard Sign

Looking to have a yard sign designed that we can place at projects we are working on. Most likely will be 18" H x 24" W but flexible that we can increase the size if necessary. It should include our logo, our phone # 609-555-0147, website rbhaldenelectric.example and slogan, built on integrity, driven by excellence. Colors should match our brand.

```html
<!DOCTYPE html>
<html lang="en">
<head>
<meta charset="utf-8">
<title>RB Halden Electric Yard Sign</title>
<link rel="stylesheet" href="https://fonts.googleapis.com/css2?family=Saira:wght@600;700&display=swap">
<style>
  :root {
    --navy: #103a63;
    --red: #d81f33;
    --white: #ffffff;
    --backdrop: #e9ebee;
  }
  html, body {
    margin: 0;
    width: 1200px;
    height: 1200px;
    overflow: hidden;
    background: var(--backdrop);
  }
  .yard-sign {
    position: absolute;
    left: 178px;
    top: 45px;
    width: 844px;
    height: 1110px;
    box-shadow: 0 10px 30px rgba(0,0,0,0.18);
  }
  .yard-sign svg { display: block; width: 100%; height: 100%; }
  .sign-text { font-family: "Saira", sans-serif; }
  .slogan-small { font-size: 50px; font-weight: 600; fill: var(--white); letter-spacing: 1px; }
  .slogan-large { font-size: 84px; font-weight: 700; fill: var(--white); }
  .company-name { font-size: 88px; font-weight: 700; fill: var(--navy); letter-spacing: 3px; }
  .company-sub { font-size: 44px; font-weight: 700; fill: var(--navy); letter-spacing: 14px; }
  .phone-number { font-size: 98px; font-weight: 700; fill: var(--navy); }
  .web-address { font-size: 44px; font-weight: 600; fill: var(--white); }
</style>
</head>
<body>
  <div class="yard-sign">
    <svg viewBox="0 0 963 1275" xmlns="http://www.w3.org/2000/svg">
      <rect class="sign-board" width="963" height="1275" fill="var(--white)"/>

      <polygon class="slogan-panel" fill="var(--navy)"
        points="0,0 670,0 730,168 635,170 815,537 0,537"/>
      <polygon class="accent-bolt" fill="var(--red)"
        points="715,18 890,22 925,293 848,300 897,645 676,200 775,195"/>

      <g class="sign-text slogan">
        <text class="slogan-small" x="90" y="140">BUILT ON</text>
        <text class="slogan-large" x="88" y="232">INTEGRITY</text>
        <text class="slogan-small" x="90" y="345">DRIVEN BY</text>
        <text class="slogan-large" x="88" y="437">EXCELLENCE</text>
      </g>

      <g class="sign-text brand-name">
        <text class="company-name" x="481" y="780" text-anchor="middle">RB HALDEN</text>
        <text class="company-sub" x="488" y="850" text-anchor="middle">ELECTRIC</text>
      </g>

      <g class="contact-phone">
        <path class="phone-icon" fill="none" stroke="var(--red)" stroke-width="14" stroke-linecap="butt"
          d="M95,990 C92,1020 110,1040 143,1043"/>
        <text class="sign-text phone-number" x="165" y="1043">609-555-0147</text>
      </g>

      <g class="contact-web">
        <rect class="web-pill" x="78" y="1078" width="817" height="95" rx="24" fill="var(--red)"/>
        <path class="cursor-icon" fill="var(--white)"
          d="M108,1110 L140,1125 L128,1130 L142,1150 L135,1154 L121,1134 L112,1142 Z"/>
        <text class="sign-text web-address" x="165" y="1142">RBHALDENELECTRIC.EXAMPLE</text>
      </g>
    </svg>
  </div>
</body>
</html>
```